Clear Plastic Card Design

I am looking to have a business card designed from my logo icon. I am looking to match the style of a different business card I have attached in the files.
Looking for a card that is plastic, with layers of transparency in the shape of my logo icon (also attached in the files) - not a circle like the other card. The winning design will incorporate the red icon logo on the front and back and include the charity's name, "Light for the Weary Souls" in the same or similar font, as well as an email and phone number. For now, use the email: email@lightfortheweary-mail.org and the phone number 555-382-7194.
We like how the sample business card has transparency, partial and full opacity layers and a matching color scheme. Files will need to be in vector so that our business card printing company can work with it.
UPDATE:
We've some excellent designs in, thank you everyone! I got an early review from the owner, and he requested a minor redirect to find his perfect design. He wants the design to stand out by NOT being a rectangle. Try instead a circle, square, or best yet - something that falls in the outline of the logo icon, either fully or partially. Thank you, everyone!
Light for the Weary Souls text should be incorporated as well as a phone and email.

```html
<!DOCTYPE html>
<html lang="en">
<head>
<meta charset="utf-8">
<title>Light for the Weary Souls – Business Card</title>
<link href="https://fonts.googleapis.com/css2?family=Lexend:wght@400&family=PT+Sans:wght@700&family=Didact+Gothic&display=swap" rel="stylesheet">
<style>
  :root {
    --backdrop: #d8dcdf;
    --frost: rgba(255, 255, 255, 0.62);
    --card-edge: #ffffff;
    --ink-dark: #111214;
    --ink-text: #1a1a1a;
    --brand-red: #c21f2b;
    --brand-orange: #e0621e;
    --contact-text: #d9d9d9;
  }
  * { margin: 0; padding: 0; box-sizing: border-box; }
  html, body { width: 1200px; height: 1008px; overflow: hidden; }
  body {
    background: var(--backdrop);
    position: relative;
  }
  .card {
    position: absolute;
    left: 220px;
    top: 124px;
    width: 760px;
    height: 760px;
  }
  .card-art {
    position: absolute;
    inset: 0;
    width: 760px;
    height: 760px;
  }
  .brand {
    position: absolute;
    left: 250px;
    top: 196px;
    width: 278px;
    text-align: right;
    font-family: "Lexend", sans-serif;
    font-weight: 400;
    font-size: 33px;
    line-height: 40px;
    color: var(--ink-text);
  }
  .brand-square {
    position: absolute;
    left: 548px;
    top: 112px;
    width: 118px;
    height: 118px;
    background: var(--brand-red);
  }
  .person-name {
    position: absolute;
    left: 64px;
    top: 520px;
    font-family: "PT Sans", sans-serif;
    font-weight: 700;
    font-size: 46px;
    color: var(--brand-orange);
    letter-spacing: 0.5px;
  }
  .contact-list {
    position: absolute;
    left: 64px;
    top: 608px;
    list-style: none;
    font-family: "Didact Gothic", sans-serif;
    font-size: 25px;
    color: var(--contact-text);
  }
  .contact-item {
    display: flex;
    align-items: center;
    gap: 12px;
    height: 42px;
  }
  .contact-icon { width: 22px; height: 22px; flex: none; }
</style>
</head>
<body>
  <div class="card">
    <svg class="card-art" viewBox="0 0 760 760" xmlns="http://www.w3.org/2000/svg" aria-hidden="true">
      <defs>
        <clipPath id="card-shape">
          <rect x="0" y="0" width="760" height="760" rx="52"/>
        </clipPath>
        <linearGradient id="swoosh" x1="0" x2="1" y1="0" y2="0">
          <stop offset="0" stop-color="#c21f2b"/>
          <stop offset="1" stop-color="#e0621e"/>
        </linearGradient>
      </defs>
      <g clip-path="url(#card-shape)">
        <rect class="card-frost" x="0" y="0" width="760" height="760" fill="var(--frost)"/>
        <path class="swoosh-top" d="M0,294 C180,286 320,350 420,405 C510,455 620,468 760,452" fill="none" stroke="url(#swoosh)" stroke-width="9"/>
        <path class="swoosh-top-thin" d="M0,280 C190,272 320,330 420,384" fill="none" stroke="var(--brand-red)" stroke-width="2"/>
        <path class="dark-panel" d="M0,326 C160,316 270,360 370,412 C470,462 590,520 760,510 L760,760 L0,760 Z" fill="var(--ink-dark)"/>
        <path class="panel-edge" d="M0,320 C160,310 270,354 370,406 C470,456 590,514 760,504" fill="none" stroke="#ffffff" stroke-width="4"/>
        <path class="swoosh-bottom" d="M500,462 C590,488 680,490 760,482" fill="none" stroke="var(--brand-red)" stroke-width="11"/>
      </g>
      <rect x="1" y="1" width="758" height="758" rx="51" fill="none" stroke="var(--card-edge)" stroke-width="3"/>
    </svg>

    <div class="brand-square"></div>
    <p class="brand">Light for the<br>Weary Souls</p>

    <h1 class="person-name">Daniel Whitford</h1>

    <ul class="contact-list">
      <li class="contact-item">
        <svg class="contact-icon" viewBox="0 0 24 24" aria-hidden="true">
          <path d="M3,9 C3,5 21,5 21,9 L18,11 L16,8 L8,8 L6,11 Z" fill="var(--brand-red)"/>
          <rect x="5" y="12" width="14" height="8" rx="1" fill="var(--brand-red)"/>
        </svg>
        <span>555-382-7194</span>
      </li>
      <li class="contact-item">
        <svg class="contact-icon" viewBox="0 0 24 24" aria-hidden="true">
          <rect x="2" y="6" width="20" height="13" fill="var(--brand-red)"/>
          <path d="M2,6 L12,13 L22,6" fill="none" stroke="var(--ink-dark)" stroke-width="1.5"/>
        </svg>
        <span>email@lightfortheweary-mail.org</span>
      </li>
    </ul>
  </div>
</body>
</html>
```